1/4 & 1/2 Page Ad For Marketing

Looking to have a ad that we can use for various community advertising requests. We are a wholesale / retail center of landscape supplies. I have attached an aerial photo of our yard some past ad content as well as our new logo designs which is the one with 6 logos which anyone can be used. Would like to be able to use in full color but also black and white.

Industry/Entity Type

Wholesale Retail of Landscape Supplies

Font styles to use
Sans Serif

Colors
59FF00
82FF00
B8FF75
E3FFCB
F4FFEA

Requirements
Must have
• Birch Hollow Yard has a wide variety of decorative stone, mulch, gravel, topsoil and sand products for all your landscaping needs. 920-555-0147 www.birchhollowyardllc.example

```html
<!DOCTYPE html>
<html lang="en">
<head>
<meta charset="utf-8">
<title>Birch Hollow Yard – Page Ads</title>
<link href="https://fonts.googleapis.com/css2?family=Montserrat:wght@500;600;700;800&family=Open+Sans:wght@400&display=swap" rel="stylesheet">
<style>
  :root{
    --lime:#59ff00;
    --lime-bright:#4be01a;
    --ink:#0d0d0d;
    --stone:#3a3b3d;
    --stone-dark:#222325;
    --sand:#d9b79a;
    --white:#ffffff;
    --label:#1a1a1a;
  }
  *{margin:0;padding:0;box-sizing:border-box}
  html,body{width:1200px;height:747px;overflow:hidden;background:var(--white)}
  body{position:relative;font-family:"Montserrat",sans-serif;color:var(--white)}
  .ad{position:absolute;overflow:hidden;background:var(--ink)}
  .ad svg.ad-art{position:absolute;inset:0;width:100%;height:100%}
  .ad-half{left:73px;top:73px;width:427px;height:552px}
  .ad-quarter{left:563px;top:136px;width:562px;height:425px}
  .brand-name{position:absolute;color:var(--lime);font-weight:800;text-align:center;line-height:1.05;text-transform:uppercase;letter-spacing:.5px}
  .web{position:absolute;font-weight:600;white-space:nowrap;display:flex;align-items:center;gap:5px}
  .web .globe{display:inline-block;border:1.5px solid var(--white);border-radius:50%;position:relative}
  .web .globe::after{content:"";position:absolute;inset:2px;border-radius:50%;background:var(--lime)}
  .web em{font-style:normal;color:var(--lime)}
  .headline{position:absolute;font-weight:700;line-height:1.22}
  .headline .lead{font-weight:600}
  .headline .hl{color:var(--lime)}
  .blurb{position:absolute;font-weight:500;line-height:1.45}
  .blurb strong{color:var(--lime);font-weight:600}
  .locale{position:absolute;font-weight:700;line-height:1.35}
  .contact-box{position:absolute;background:var(--lime-bright);border-radius:6px 0 0 6px;padding-left:14px;display:flex;flex-direction:column;justify-content:center}
  .contact-box .phone{font-weight:800;color:var(--white);display:flex;align-items:center;gap:4px}
  .contact-box .addr{font-weight:500;color:var(--white);display:flex;align-items:center;gap:4px}
  .size-label{position:absolute;top:658px;font-family:"Open Sans",sans-serif;font-size:29px;color:var(--label);width:300px;text-align:center}
</style>
</head>
<body>

<!-- Half page ad -->
<section class="ad ad-half">
  <svg class="ad-art" viewBox="0 0 427 552" aria-hidden="false">
    <defs>
      <linearGradient id="yardH" x1="0" y1="0" x2="1" y2="1">
        <stop offset="0" stop-color="#cdb6a0"/><stop offset=".5" stop-color="#dcbfa3"/><stop offset="1" stop-color="#a8734f"/>
      </linearGradient>
      <linearGradient id="stoneH" x1="0" y1="0" x2="0" y2="1">
        <stop offset="0" stop-color="#45464a"/><stop offset="1" stop-color="#2a2b2d"/>
      </linearGradient>
    </defs>
    <path role="img" aria-label="Aerial photo of the landscape supply yard" fill="url(#yardH)" d="M0,240 C60,180 180,150 300,120 C370,100 410,60 427,30 L427,552 L0,552 Z"/>
    <path fill="var(--lime)" d="M40,232 C110,170 230,150 320,120 C380,95 410,60 427,20 L427,45 C400,95 350,125 300,140 C200,168 110,185 40,232 Z"/>
    <path role="img" aria-label="Dark river stone texture" fill="url(#stoneH)" d="M0,552 L0,470 C40,420 120,410 200,420 C290,430 360,400 400,340 L427,300 L427,552 Z"/>
    <path fill="var(--lime)" d="M0,552 L32,552 C50,480 85,440 130,420 L110,412 C60,430 20,470 0,520 Z"/>
    <path fill="var(--lime)" d="M427,290 C415,330 395,360 370,378 L385,386 C405,365 420,340 427,318 Z"/>
    <g stroke="var(--lime)" stroke-width="4">
      <circle role="img" aria-label="Garden bed with red flowers" cx="124" cy="397" r="33" fill="#8a6a5a"/>
      <circle role="img" aria-label="Pile of shredded mulch" cx="220" cy="380" r="50" fill="#8e5f48"/>
      <circle role="img" aria-label="Green delivery truck with mulch piles" cx="347" cy="350" r="66" fill="#7a8a5a"/>
    </g>
  </svg>
  <div class="brand-name" style="left:18px;top:44px;width:160px;font-size:18px">Birch Hollow<br>Yard</div>
  <div class="web" style="left:170px;top:37px;font-size:12.5px"><span class="globe" style="width:14px;height:14px"></span>www.<em>birchhollowyardllc</em>.example</div>
  <div class="headline" style="left:99px;top:443px">
    <div class="lead" style="font-size:18px">We are a</div>
    <div style="font-size:14.5px"><span class="hl">Whole sale</span> / <span class="hl">Retail center</span></div>
    <div style="font-size:14.5px">of landscape supplies</div>
  </div>
  <p class="blurb" style="left:99px;top:504px;width:190px;font-size:7.3px"><strong>Birch Hollow Yard</strong> has a wide variety of decorative stone, mulch, gravel, topsoil and sand products for all your landscaping needs.</p>
  <p class="locale" style="left:306px;top:456px;width:120px;font-size:7.4px">Located between maple ridge and fox falls where hwy 12 and hwy kk meet!</p>
  <div class="contact-box" style="left:295px;top:497px;width:132px;height:35px;padding-left:16px">
    <div class="phone" style="font-size:12.5px"><svg width="8" height="8" viewBox="0 0 10 10"><path fill="#fff" d="M2 0 L4 2.5 L3 3.8 C3.8 5.4 4.8 6.4 6.2 7 L7.5 6 L10 8 L8.5 10 C4 9.5 .5 6 0 1.5Z"/></svg>920-555-0147</div>
    <div class="addr" style="font-size:5px"><svg width="6" height="7" viewBox="0 0 10 12"><path fill="#fff" d="M5 0a4.5 4.5 0 0 0-4.5 4.5C.5 8 5 12 5 12s4.5-4 4.5-7.5A4.5 4.5 0 0 0 5 0zm0 6.5a2 2 0 1 1 0-4 2 2 0 0 1 0 4z"/></svg>1480 Quarry Ln. Fox Falls, WI 54000</div>
  </div>
</section>

<!-- Quarter page ad -->
<section class="ad ad-quarter">
  <svg class="ad-art" viewBox="0 0 562 425">
    <defs>
      <linearGradient id="yardQ" x1="0" y1="0" x2="1" y2="1">
        <stop offset="0" stop-color="#c9b39e"/><stop offset=".5" stop-color="#dcc0a4"/><stop offset="1" stop-color="#a6744f"/>
      </linearGradient>
      <linearGradient id="stoneQ" x1="0" y1="0" x2="0" y2="1">
        <stop offset="0" stop-color="#47484c"/><stop offset="1" stop-color="#2a2b2d"/>
      </linearGradient>
    </defs>
    <path role="img" aria-label="Aerial photo of the landscape supply yard" fill="url(#yardQ)" d="M0,200 C50,130 200,115 350,95 C450,80 530,40 562,5 L562,425 L0,425 Z"/>
    <path fill="var(--lime)" d="M45,140 C130,105 260,95 380,78 C470,62 535,35 562,2 L562,18 C530,55 470,80 390,95 C260,112 140,115 45,140 Z"/>
    <path role="img" aria-label="Dark river stone texture" fill="url(#stoneQ)" d="M40,425 C90,320 200,290 300,290 C400,290 480,270 530,230 L562,200 L562,425 Z"/>
    <path fill="var(--lime)" d="M0,425 L40,425 C70,350 130,310 230,296 L300,292 L300,282 L220,286 C110,296 40,340 0,395 Z"/>
    <path fill="var(--lime)" d="M562,185 C545,225 520,250 490,270 L500,276 C530,258 552,235 562,212 Z"/>
    <g stroke="var(--lime)" stroke-width="3.5">
      <circle role="img" aria-label="Garden bed with red flowers" cx="310" cy="290" r="25" fill="#8a6a5a"/>
      <circle role="img" aria-label="Pile of shredded mulch" cx="383" cy="278" r="38" fill="#8e5f48"/>
      <circle role="img" aria-label="Green delivery truck with mulch piles" cx="481" cy="253" r="50" fill="#7a8a5a"/>
    </g>
  </svg>
  <div class="brand-name" style="left:12px;top:36px;width:150px;font-size:16px">Birch Hollow<br>Yard</div>
  <div class="web" style="left:213px;top:20px;font-size:14.5px"><span class="globe" style="width:16px;height:16px"></span>www.<em>birchhollowyardllc</em>.example</div>
  <div class="headline" style="left:166px;top:316px">
    <div class="lead" style="font-size:18px">We are a</div>
    <div style="font-size:14.5px"><span class="hl">Whole sale</span> / <span class="hl">Retail center</span></div>
    <div style="font-size:14.5px">of landscape supplies</div>
  </div>
  <p class="blurb" style="left:166px;top:381px;width:200px;font-size:7.3px"><strong>Birch Hollow Yard</strong> has a wide variety of decorative stone, mulch, gravel, topsoil and sand products for all your landscaping needs.</p>
  <p class="locale" style="left:411px;top:324px;width:140px;font-size:8px">Located between maple ridge and fox falls where hwy 12 and hwy kk meet!</p>
  <div class="contact-box" style="left:404px;top:366px;width:158px;height:40px;padding-left:20px">
    <div class="phone" style="font-size:13.5px"><svg width="8" height="8" viewBox="0 0 10 10"><path fill="#fff" d="M2 0 L4 2.5 L3 3.8 C3.8 5.4 4.8 6.4 6.2 7 L7.5 6 L10 8 L8.5 10 C4 9.5 .5 6 0 1.5Z"/></svg>920-555-0147</div>
    <div class="addr" style="font-size:5.2px"><svg width="6" height="7" viewBox="0 0 10 12"><path fill="#fff" d="M5 0a4.5 4.5 0 0 0-4.5 4.5C.5 8 5 12 5 12s4.5-4 4.5-7.5A4.5 4.5 0 0 0 5 0zm0 6.5a2 2 0 1 1 0-4 2 2 0 0 1 0 4z"/></svg>1480 Quarry Ln. Fox Falls, WI 54000</div>
  </div>
</section>

<div class="size-label" style="left:136px">1/2 Page Ad</div>
<div class="size-label" style="left:693px">1/4 Page Ad</div>

</body>
</html>
```